Brochure Design Project

We need a brochure for our acting school, website is
www.stagelarkhouse.com - It needs to reflect youth, vitality, and people's DREAMS coming true...colors should be red and black, but open to something new as well...the courses included should be
Players' Rapid Forge, Steady Stage Bundle, And The Mastery Track

Emphasis on Players' Rapid Forge is the short term intensity.
Steady Stage Bundle is the benefit of getting all the tools to look for acting work.
Mastery Track is becoming a pro, and if you are in another country, being provided with a visa to come to the U.S.

I have attached pictures and logos...I will submit the copy once there is a framework...the OLD brochure is attached as well...

Thank you...

Marlon

Reason: We would like to see a couple more ideas...

Reason: HI there designers! Thanks for your submissions. We are almost ready to pick a design. Thanks for the understanding.

Target Market(s)

18-35 year olds...fairly affluent, educated, American, European, or Australian

Industry/Entity Type

School

Requirements
Must have
• Make it fun, clean, clear, and NOT corporate.

```html
<!DOCTYPE html>
<html lang="en">
<head>
<meta charset="utf-8">
<title>Stagelark House – Programs Brochure</title>
<link rel="stylesheet" href="https://fonts.googleapis.com/css2?family=Archivo+Black&family=Open+Sans:wght@400;600;700&display=swap">
<style>
  :root {
    --ink: #141414;
    --red: #c8102e;
    --paper: #ececec;
    --paper-dark: #d6d6d6;
    --text: #3a3a3a;
    --brand-grey: #5a5a5a;
    --white: #ffffff;
    --stage-dark: #1c1410;
    --stage-warm: #6b4a2e;
  }
  * { box-sizing: border-box; margin: 0; padding: 0; }
  html, body { width: 1200px; height: 863px; overflow: hidden; background: #ffffff; }
  body { position: relative; font-family: "Open Sans", Arial, sans-serif; color: var(--text); }

  .spread { position: absolute; left: 60px; top: 130px; width: 780px; height: 600px; box-shadow: 0 6px 18px rgba(0,0,0,.18); }
  .panel {
    position: absolute; top: 130px; width: 260px; height: 600px;
    background: linear-gradient(155deg, #f4f4f4 0%, var(--paper) 35%, var(--paper-dark) 60%, #efefef 100%);
    overflow: hidden;
  }
  .panel--programs { left: 60px; }
  .panel--bundle { left: 320px; border-left: 1px solid #d0d0d0; }
  .panel--mastery { left: 580px; border-left: 1px solid #d0d0d0; }
  .panel--cover { left: 890px; box-shadow: 0 6px 18px rgba(0,0,0,.18); }

  .stage-photo {
    position: absolute; height: 70px;
    background: radial-gradient(ellipse at 40% 60%, var(--stage-warm) 0%, var(--stage-dark) 70%);
  }
  .red-bar { position: absolute; background: var(--red); }

  /* Section title */
  .section-title { position: absolute; left: 14px; top: 40px; }
  .section-title__line {
    display: block; width: max-content; background: var(--ink); color: var(--white);
    font-family: "Archivo Black", Arial, sans-serif; font-size: 33px; line-height: 36px;
    padding: 0 6px; margin-bottom: 3px; text-transform: uppercase;
  }
  .section-title__tag {
    display: inline-block; margin-left: 60px; background: var(--red); color: var(--white);
    font-family: "Open Sans", Arial, sans-serif;
    font-size: 8px; font-weight: 700; letter-spacing: 1px; padding: 1px 10px; text-transform: uppercase;
  }

  /* Program blocks */
  .program { position: absolute; left: 14px; right: 14px; }
  .program__head { display: flex; align-items: flex-start; gap: 8px; }
  .program__label { display: inline-block; }
  .program__label--right { display: block; margin-left: auto; width: max-content; }
  .program__name {
    display: block; width: max-content; background: var(--ink); color: var(--white);
    font-family: "Archivo Black", Arial, sans-serif; font-size: 11px; line-height: 17px;
    padding: 0 8px; text-transform: uppercase;
  }
  .program__length {
    display: block; width: max-content; margin-left: auto; background: var(--red); color: var(--white);
    font-size: 7px; font-weight: 700; letter-spacing: .8px; padding: 0 8px; line-height: 11px; text-transform: uppercase;
  }
  .badge { width: 40px; height: 34px; background: var(--ink); border-radius: 4px; margin-left: auto; }
  .program__body { font-size: 7.2px; line-height: 10.6px; margin-top: 8px; }
  .program__body p + p { margin-top: 8px; }

  /* Cover */
  .brand { position: absolute; top: 52px; left: 0; width: 100%; display: flex; justify-content: center; align-items: center; gap: 8px; }
  .brand__dot { width: 9px; height: 9px; border-radius: 50%; background: var(--brand-grey); }
  .brand__name { font-family: "Archivo Black", Arial, sans-serif; font-size: 17px; color: var(--brand-grey); letter-spacing: 1px; }

  .headline {
    position: absolute; left: 16px; top: 160px; right: 10px;
    font-family: "Archivo Black", Arial, sans-serif; font-weight: 400;
    color: var(--ink); font-size: 54px; line-height: 68px; text-transform: uppercase;
  }
  .headline__line { display: block; }
  .headline__line--first { margin-left: 140px; }
  .headline__line--last { font-size: 48px; }

  .tagline { position: absolute; left: 14px; top: 480px; }
  .tagline__title { font-family: "Archivo Black", Arial, sans-serif; font-size: 14px; color: var(--ink); text-transform: uppercase; }
  .tagline__sub { font-size: 13px; color: var(--red); font-weight: 600; margin-left: 104px; }
</style>
</head>
<body>
  <div class="spread"></div>

  <!-- Inside panel 1 -->
  <section class="panel panel--programs">
    <h1 class="section-title">
      <span class="section-title__line">What</span>
      <span class="section-title__line">We do</span>
      <span class="section-title__line">About it</span>
      <span class="section-title__tag">★ Programs ★</span>
    </h1>

    <article class="program" style="top:200px;">
      <div class="program__head">
        <div class="program__label">
          <h2 class="program__name">Boot Camp I</h2>
          <span class="program__length">4 weeks</span>
        </div>
        <div class="badge" role="img" aria-label="Program badge"></div>
      </div>
      <div class="program__body">
        <p>The Players' Rapid Forge, created by Artistic Director Marlon Dravik, with over 1,200 graduates on CastIndex, offers an alternative to acting teacher worship: no fees, 90 minutes on your feet, daily actors' training. We acknowledge the 21st century by offering only the practical and useful elements of the Halvard Technique and the Ansel Brevik Technique, as well as the practical application of all this to cold reading and scene study.</p>
        <p>The Players' Rapid Forge is four weeks of daily classes, by the end of which you will know if acting is your life's work or just a passing fancy.</p>
      </div>
    </article>

    <article class="program" style="top:405px;">
      <div class="program__head">
        <div class="program__label">
          <h2 class="program__name">Boot Camp II</h2>
          <span class="program__length">6 weeks</span>
        </div>
        <div class="badge" role="img" aria-label="Program badge"></div>
      </div>
      <div class="program__body">
        <p>The Army's Boot Camp prepares you for war. The Players' Rapid Forge II prepares you for a much tougher battle – Show Business: that's why it's six glorious weeks of daily work. After Boot Camp II, you will never again be able to return to civilian life; you are now an actor. Here you will continue to learn and apply only the relevant aspects of the Halvard Technique and the Ansel Brevik Technique, you will learn true on-camera skills so that you can work on any type of shoot, and you will learn and APPLY business tools that will get you going in your career.</p>
      </div>
    </article>
  </section>

  <!-- Inside panel 2 -->
  <section class="panel panel--bundle">
    <div class="stage-photo" style="left:18px; right:0; top:40px;" role="img" aria-label="Photo of actors performing on a stage"></div>
    <div class="red-bar" style="left:0; top:140px; width:8px; height:70px;"></div>

    <article class="program" style="top:128px;">
      <div class="program__label program__label--right">
        <h2 class="program__name">The Steady Stage Bundle</h2>
        <span class="program__length">3 months</span>
      </div>
      <div class="program__body">
        <p>There are those who come to Hollywood, manage to get an audition, go in hoping for the best, and fail miserably. While there is something to be said for that kind of moxie, there's also something to be said for not burning bridges. Meaning you only get one shot at a relationship with a casting director, director, or producer. So give it your best.</p>
        <p>The Steady Stage Bundle, Boot Camp I and II back to back, giving you everything you need to book the job, including a personalized way to market yourself. It will leave you with one thing: NO EXCUSES. So what are you waiting for?</p>
      </div>
    </article>

    <article class="program" style="top:345px;">
      <div class="program__label program__label--right">
        <h2 class="program__name">The Advanced Program</h2>
        <span class="program__length">Ongoing</span>
      </div>
      <div class="program__body">
        <p>Only auditioning, committed actors are invited to The Advanced Program. Why? Because we spare no effort or expense in getting you in shape and in front of agents, managers and casting directors. During on-going courses, you will gain a deep understanding of character and script analysis, as well as invaluable experience playing many different kinds of parts in all of the genres you might audition for in today's industry.</p>
      </div>
    </article>
  </section>

  <!-- Inside panel 3 -->
  <section class="panel panel--mastery">
    <div class="stage-photo" style="left:0; right:14px; top:20px; height:82px;" role="img" aria-label="Photo of a theatre entrance and actors rehearsing at night"></div>
    <div class="red-bar" style="right:0; top:20px; width:8px; height:82px;"></div>

    <article class="program" style="top:118px;">
      <div class="program__label program__label--right">
        <h2 class="program__name">The Mastery Track</h2>
        <span class="program__length">9 months</span>
      </div>
      <div class="program__body">
        <p>Designed for actors who come to Los Angeles and are committed to turning their dreams into reality, the nine-month Mastery Track gets you working on your acting 20 hours a week, every week.</p>
        <p>Utilizing only the effective and updated elements of the Halvard and Ansel Brevik techniques, you will learn the Stagelark House technique and its acting fundamentals, applying it to any role and every audition. You will also learn how to read and prepare any script, so that you can walk into the stage, camera or audition room and book the job.</p>
        <p>At the end of the nine-month program you will receive a Mastery Track certificate of completion.</p>
        <p>If you are an international student, a portion of The Mastery Track qualifies for visa sponsorship and we will do our best to help you.</p>
      </div>
    </article>
  </section>

  <!-- Front cover -->
  <section class="panel panel--cover">
    <div class="brand">
      <span class="brand__dot"></span>
      <span class="brand__name">STAGELARK HOUSE</span>
    </div>

    <div class="stage-photo" style="left:0; width:136px; top:165px; height:64px;" role="img" aria-label="Photo of a lit stage with an audience"></div>
    <div class="red-bar" style="left:138px; top:165px; width:8px; height:64px;"></div>

    <h2 class="headline">
      <span class="headline__line headline__line--first">If</span>
      <span class="headline__line">Not</span>
      <span class="headline__line">Now,</span>
      <span class="headline__line headline__line--last">When?</span>
    </h2>

    <div class="tagline">
      <p class="tagline__title">Players' Rapid Forge</p>
      <p class="tagline__sub">Play your life</p>
    </div>
    <div class="red-bar" style="right:0; top:478px; width:14px; height:34px;"></div>
  </section>
</body>
</html>
```